"Inked for Trouble"--book cover for a light cozy mystery

The book is titled INKED FOR TROUBLE (subtitle; A Harold Penwick Puzzle), author: R. T. Halvorsen.

Here is the synopsis which will also appear on the back cover:

“Eight years after Birchfield Academy’s Humanities Chairperson (Cyril Webb) was murdered, Professor Harold Penwick is now in that position, and history appears to be doing its repetitive thing. With one of his dogs aging and the “new” one engaging, Penny must solve the murders or become another victim.”

I would need a front cover that expresses the feel of the book. Here are some ideas from the author:

1. Crimson colored
2. Should show Brisk the main character's dog in front. Brisk should look like an all-white beagle with a pony’s white mane from the top of her head partly down her back (a beagle/wire terrier mix).
3. The book title should be higher up, and displayed on a chalkboard which also shows some writing from a "teacher" such as: Semicolon = Balance, Colon = Introduce Statement
4. A shadow of the killer should show behind our transposed on top of the front. The shadow of the killer should feature the person's hands reaching out as if to strangle someone."

The author wants a cover similar to his first book in the Harold Penwick mystery series which was entitled LAWS OF THE LAST. I can send jpg of this book and the second in the series, but you may have some thoughts of your own which is fine.

I have a subscription with PixVault.example so it would be very helpful if you would draw any images you use from their "Basics" collection (not their "Premier" collection which I can't afford.) Once we decide on a final cover, you can just send me the ID numbers of the images you need and I will download them and send them to you.

Ultimately, I will need two things: a jpg of the front cover that is at least 1600 pixels wide for upload to Leafreader. Our book covers are all 6" wide x 9" high. We will also need a full cover completed using a template from PrintNest which I will send later that uses the front cover you design plus a spine that shows (from top to bottom) the author's name, the book title, and our logo. I will also send you our logo for your use. The back of the full cover includes the short synopsis from above which should be justified and in a readable font, and our logo in the lower left-hand corner. The lower right hand corner of the back cover is reserved for the ISBN which the printer will add later.

We don't have a very large budget for covers, but we produce quite a few on a regular basis and if we like your work and your work ethic, it could easily become an on-going relationship.

Sincerely,

Helen Strand
Publisher
Quiet Owl Books

Target Market(s)

adult readers of light mysteries

Industry/Entity Type

Book Publisher

Colors
f04a50

Requirements
Must have
• 1. front cover jpg for a 6" x 9" book (1600 pixels on short side)
• 2. full cover with the design on front, title, author and our logo on spine and synopsis and logo on back cover. To be placed on a template provided by me from PrintNest and provided to me as a pdf
• Note: I have a subscription with PixVault.example using their Basics collection so it would be very helpful if artist selected imagery from this collection. Once design is approved I will be able to download the images the artist needs from PixVault and send them to the designer.
Nice to have
• See project description above.
• Our books at Quiet Owl Books are all mysteries, so we like covers to look mysterious, but they are also light so we don't want them to be too bloody or gory.

```html
<!DOCTYPE html>
<html lang="en">
<head>
<meta charset="utf-8">
<title>Inked for Trouble — Front Cover and Spine</title>
<link rel="stylesheet" href="https://fonts.googleapis.com/css2?family=Cabin+Sketch:wght@400;700&family=Schoolbell&family=Open+Sans:wght@600;700&display=swap">
<style>
  :root {
    --backdrop: #e9e4de;
    --crimson-deep: #4a1016;
    --crimson: #6b1b22;
    --crimson-glow: #7f252c;
    --board: #2b2b2b;
    --board-edge: #1c1c1c;
    --frame: #4a2a17;
    --frame-light: #6a3f22;
    --chalk: #eeeeea;
    --chalk-faint: rgba(238, 238, 234, 0.75);
    --desk-dark: #141414;
    --desk-wood: #b8702f;
    --fur: #e8e4dc;
    --text-light: #f4f1ec;
  }
  * { box-sizing: border-box; margin: 0; padding: 0; }
  html, body {
    width: 1200px; height: 1091px; overflow: hidden;
    background: var(--backdrop);
  }
  .book {
    position: absolute; left: 235px; top: 50px;
    width: 730px; height: 990px;
    display: flex;
    box-shadow: 0 10px 30px rgba(0,0,0,0.25);
  }
  .spine {
    position: relative; width: 70px; height: 100%;
    background: linear-gradient(90deg, var(--crimson-deep), var(--crimson) 60%, var(--crimson-deep));
    border-right: 1px solid rgba(0,0,0,0.4);
  }
  .spine-text {
    position: absolute; left: 50%; top: 40px;
    transform-origin: 0 0;
    transform: rotate(90deg) translateY(-50%);
    white-space: nowrap;
    display: flex; align-items: center; gap: 70px;
    color: var(--text-light);
  }
  .spine-author { font-family: "Open Sans", sans-serif; font-weight: 600; font-size: 30px; }
  .spine-title { font-family: "Cabin Sketch", cursive; font-size: 34px; }
  .spine-imprint {
    position: absolute; bottom: 22px; left: 0; width: 100%;
    display: flex; flex-direction: column; align-items: center; gap: 5px;
    font-family: "Open Sans", sans-serif; font-weight: 600;
    font-size: 8px; line-height: 1.15; text-align: center; color: var(--text-light);
  }
  .spine-imprint .mark {
    width: 14px; height: 14px; border-radius: 50%; background: var(--text-light);
  }
  .front {
    position: relative; width: 660px; height: 100%; overflow: hidden;
    background:
      radial-gradient(ellipse at 50% 35%, var(--crimson-glow) 0%, var(--crimson) 45%, var(--crimson-deep) 100%);
  }
  .series-line {
    position: absolute; top: 26px; left: 0; width: 100%;
    text-align: center;
    font-family: "Schoolbell", cursive; font-size: 30px;
    color: var(--text-light); letter-spacing: 0.5px;
  }
  .chalkboard {
    position: absolute; left: 56px; top: 140px; width: 500px; height: 300px;
    background: var(--frame);
    border: 3px solid var(--frame-light);
    padding: 12px;
    box-shadow: 4px 6px 14px rgba(0,0,0,0.5);
  }
  .chalkboard-surface {
    position: relative; width: 100%; height: 100%;
    background: radial-gradient(ellipse at 40% 40%, #3a3a3a, var(--board) 60%, var(--board-edge));
    overflow: hidden;
  }
  .book-title {
    position: absolute; left: 30px; top: 18px;
    font-family: "Cabin Sketch", cursive; font-weight: 400;
    font-size: 74px; line-height: 0.98; color: var(--chalk);
    transform: rotate(-4deg);
  }
  .book-title .line-two { display: block; padding-left: 95px; }
  .chalk-notes {
    position: absolute; left: 150px; top: 180px;
    font-family: "Schoolbell", cursive; font-size: 21px; line-height: 1.2;
    color: var(--chalk-faint);
    transform: rotate(-5deg);
  }
  .chalk-notes p:first-child { padding-left: 40px; }
  .killer-shadow {
    position: absolute; left: 430px; top: 90px; width: 230px; height: 330px;
    background: radial-gradient(ellipse at 55% 45%, rgba(15,5,6,0.55), rgba(15,5,6,0.2) 55%, rgba(15,5,6,0) 75%);
  }
  .desk-area {
    position: absolute; left: 0; top: 700px; width: 660px; height: 290px;
    background: var(--desk-dark);
  }
  .desk-chair {
    position: absolute; left: 380px; top: 720px; width: 260px; height: 150px;
    background: linear-gradient(180deg, #c67f3a, var(--desk-wood) 60%, #8f531f);
    border-radius: 6px;
  }
  .dog-photo {
    position: absolute; left: 10px; top: 730px; width: 300px; height: 260px;
    background: radial-gradient(ellipse at 50% 45%, #f6f3ee, var(--fur) 55%, #b9b3a8);
    border-radius: 45% 45% 0 0;
  }
  .author-name {
    position: absolute; left: 280px; top: 880px;
    font-family: "Open Sans", sans-serif; font-weight: 700; font-size: 34px;
    color: var(--text-light);
    text-shadow: 2px 2px 4px rgba(0,0,0,0.8);
  }
</style>
</head>
<body>
  <div class="book">
    <div class="spine">
      <div class="spine-text">
        <span class="spine-author">R. T. Halvorsen</span>
        <span class="spine-title">Inked for Trouble</span>
      </div>
      <div class="spine-imprint">
        <span class="mark"></span>
        <span>Quiet Owl<br>Books</span>
      </div>
    </div>
    <div class="front">
      <div class="series-line">A Harold Penwick Puzzle</div>
      <div class="chalkboard">
        <div class="chalkboard-surface">
          <h1 class="book-title">Inked for<span class="line-two">Trouble</span></h1>
          <div class="chalk-notes">
            <p>Semicolon = Balance</p>
            <p>Colon = Introduce Statement</p>
          </div>
        </div>
      </div>
      <div class="killer-shadow" role="img" aria-label="Shadow of the killer's hand reaching across the chalkboard"></div>
      <div class="desk-area"></div>
      <div class="desk-chair" role="img" aria-label="Wooden classroom chair in the dark lower right"></div>
      <div class="dog-photo" role="img" aria-label="Photo of Brisk, a small white shaggy dog, at the front"></div>
      <div class="author-name">R. T. Halvorsen</div>
    </div>
  </div>
</body>
</html>
```